Brisk Hound Signage

This design is for "signage" that we intend to get produced.
A couple of different designs that say "Brisk Hound on Guard" and "Beware of Brisk Hound"
It should also have our logo (BH) plus our logo with the hand and dog paw. We would also like the main picture of the sign to be the attached. We would like a classy sophisticated look similar to our logo you designed.
Our designs will go on consumers gates/entrances to warn people there is a dog on the premises. I will get a better quality picture of the dog.

```html
<!DOCTYPE html>
<html lang="en">
<head>
<meta charset="utf-8">
<title>Brisk Hound Signage</title>
<link rel="stylesheet" href="https://fonts.googleapis.com/css2?family=Jost:wght@400;700&display=swap">
<style>
  :root {
    --bg: #e4e4e4;
    --sign-white: #ffffff;
    --ring: #9ea9da;
    --ink-dark: #3b3333;
    --ink-black: #111111;
    --dog-dark: #2e2e2e;
    --dog-mid: #4a4a4a;
    --shadow: rgba(0,0,0,0.18);
  }
  * { margin: 0; padding: 0; box-sizing: border-box; }
  html, body {
    width: 1200px;
    height: 2879px;
    overflow: hidden;
    background: var(--bg);
    font-family: "Jost", "Futura", sans-serif;
  }
  .signage-sheet {
    width: 1200px;
    height: 2879px;
    display: flex;
    flex-direction: column;
    align-items: center;
    justify-content: space-evenly;
  }
  .sign {
    position: relative;
    width: 640px;
    height: 640px;
    border-radius: 50%;
    background: var(--sign-white);
    box-shadow: 0 10px 30px var(--shadow);
  }
  .sign-ring {
    position: absolute;
    inset: 28px;
    border-radius: 50%;
    border: 3px solid var(--ring);
  }
  .sign-content {
    position: absolute;
    inset: 0;
    display: flex;
    flex-direction: column;
    align-items: center;
    padding-top: 72px;
  }
  .dog-photo {
    width: 190px;
    height: 200px;
    border-radius: 46% 46% 18% 18%;
    background: radial-gradient(ellipse at 45% 35%, var(--dog-mid), var(--dog-dark) 70%);
    box-shadow: 0 26px 22px -14px rgba(0,0,0,0.28);
  }
  .headline {
    margin-top: 58px;
    text-align: center;
    line-height: 1;
  }
  .headline-bold {
    display: block;
    font-weight: 700;
    font-size: 56px;
    letter-spacing: 2px;
  }
  .headline-light {
    display: block;
    font-weight: 400;
    font-size: 51px;
    letter-spacing: 2px;
  }
  .headline-rule {
    display: block;
    height: 3px;
    background: var(--ring);
    margin: 6px 0 8px;
  }
  .sign--beware .headline { color: var(--ink-dark); }
  .sign--guard .headline { color: var(--ink-black); }
  .brand-row {
    margin-top: 26px;
    display: flex;
    gap: 18px;
  }
  .brand-mark {
    width: 74px;
    height: 74px;
    border-radius: 50%;
    border: 2px solid var(--ring);
    display: flex;
    align-items: center;
    justify-content: center;
    color: var(--ring);
    font-weight: 400;
    text-align: center;
  }
  .brand-mark--name { font-size: 11px; line-height: 1.15; letter-spacing: 0.5px; }
  .brand-mark--initials { font-size: 26px; }
</style>
</head>
<body>
<main class="signage-sheet">

  <section class="sign sign--beware">
    <div class="sign-ring"></div>
    <div class="sign-content">
      <div class="dog-photo" role="img" aria-label="Photo of a seated black dog"></div>
      <h1 class="headline">
        <span class="headline-bold">BEWARE OF</span>
        <span class="headline-rule"></span>
        <span class="headline-light">BRISK HOUND</span>
      </h1>
      <div class="brand-row">
        <div class="brand-mark brand-mark--name">BRISK<br>HOUND</div>
        <div class="brand-mark brand-mark--initials">BH</div>
      </div>
    </div>
  </section>

  <section class="sign sign--guard">
    <div class="sign-ring"></div>
    <div class="sign-content">
      <div class="dog-photo" role="img" aria-label="Photo of a seated black dog"></div>
      <h1 class="headline">
        <span class="headline-light">BRISK HOUND</span>
        <span class="headline-rule"></span>
        <span class="headline-bold">ON GUARD</span>
      </h1>
      <div class="brand-row">
        <div class="brand-mark brand-mark--name">BRISK<br>HOUND</div>
        <div class="brand-mark brand-mark--initials">BH</div>
      </div>
    </div>
  </section>

</main>
</body>
</html>
```